stationary deign for trucking company

im a trucking company looking for a professional set of stationary designs i deliver goods from point a to b
Updates

When submitting stationary designs I need envelope design, letterhead, cards, I’d badge etc

Industry/Entity Type

Trucking Company

Requirements
Must have
• must have letter head, business card, envelope, fax sheet, id badge, folder, thank you card, notebook, invoice sheet.
Nice to have
• nice to have them all custom made (letterhead,envelope, business card, I’d badge etc
Should not have
• must not have prepaid sign want i unique design for items

```html
<!DOCTYPE html>
<html lang="en">
<head>
<meta charset="utf-8">
<title>Harlow Transportation · Logistics — Stationery Set</title>
<link href="https://fonts.googleapis.com/css2?family=Montserrat:wght@400;600&family=Open+Sans:wght@400;600&display=swap" rel="stylesheet">
<style>
  :root{
    --bg:#e3e5e7;
    --paper:#ffffff;
    --ink:#1b1b1d;
    --blue:#1f5fbf;
    --muted:#5a5f66;
    --label:#3d5878;
    --faint:#dfe3e8;
    --faint-blue:#dbe6f3;
    --black:#0c0c0e;
    --window:#e6e6e6;
  }
  *{box-sizing:border-box;margin:0;padding:0}
  html,body{width:737px;height:1200px;overflow:hidden}
  body{background:var(--bg);font-family:"Open Sans",Arial,sans-serif;color:var(--ink);position:relative}
  .piece{position:absolute;background:var(--paper);box-shadow:0 2px 6px rgba(0,0,0,.12);overflow:hidden}
  .label{position:absolute;font-size:12.5px;color:var(--label);text-align:center}
  .brand{font-family:"Montserrat",Arial,sans-serif;font-weight:600;color:var(--ink);letter-spacing:.14em;line-height:1;display:flex;align-items:center;gap:5px}
  .brand .dot{display:inline-block;background:var(--blue)}
  .brand small{display:block;font-weight:400;font-size:.32em;letter-spacing:.22em;margin-top:3px}
  .faint-mark{position:absolute;border-radius:50%;border:6px solid var(--faint)}
  .tiny{font-size:4.4px;line-height:1.55;color:var(--muted)}
  .tiny b{color:var(--blue);font-weight:600}
  .contact-col{position:absolute;display:flex;gap:6px}
  .contact-col .rule{width:1px;background:var(--blue)}
  /* business cards */
  .card-front{left:68px;top:69px;width:130px;height:74px}
  .card-front .card-contact{position:absolute;left:10px;top:27px;line-height:1.45;white-space:nowrap}
  .card-back{left:216px;top:69px;width:130px;height:74px;background:var(--black)}
  .card-back .brand{color:var(--blue);position:absolute;left:26px;top:30px;font-size:9px}
  .card-back .web{position:absolute;bottom:7px;width:100%;text-align:center;font-size:3.6px;color:#9aa0a8}
  /* letterheads */
  .letterhead{left:73px;top:175px;width:264px;height:370px}
  .letter{left:385px;top:177px;width:285px;height:368px}
  .letter .body{position:absolute;left:18px;top:160px;width:250px;font-size:4.6px;line-height:1.75;color:#444}
  .letter .body p{margin-bottom:6px}
  .signature{width:40px;height:12px;background:linear-gradient(90deg,#e9ebee,#d7dbe0);margin:3px 0}
  /* envelopes */
  .env-front{left:25px;top:601px;width:338px;height:151px}
  .env-window{position:absolute;left:20px;top:84px;width:124px;height:46px;border-radius:4px;background:var(--window)}
  .env-back{left:378px;top:601px;width:334px;height:149px}
  .env-flap{position:absolute;left:0;top:0}
  /* id card */
  .id-card{left:296px;top:900px;width:146px;height:226px;border-radius:6px;padding-top:18px;text-align:center}
  .photo{width:50px;height:50px;margin:16px auto 0;background:linear-gradient(160deg,#c9d3de,#6f7d8c);border:2px solid var(--blue)}
  .id-name{font-family:"Montserrat",Arial,sans-serif;font-weight:600;font-size:6.5px;color:var(--blue);margin-top:12px;letter-spacing:.04em}
  .id-role{font-size:4.6px;color:var(--muted)}
  .id-table{margin:10px 0 0 42px;text-align:left;font-size:4.5px;line-height:1.55;color:var(--muted)}
  .id-table span{display:inline-block;width:20px;color:var(--blue)}
</style>
</head>
<body>

<!-- Business card -->
<section class="piece card-front">
  <div class="faint-mark" style="left:84px;top:12px;width:52px;height:52px;border-width:4px"></div>
  <div class="brand" style="position:absolute;left:10px;top:9px;font-size:7px"><span class="dot" style="width:6px;height:6px"></span><span>HARLOW<small>TRANSPORTATION · LOGISTICS</small></span></div>
  <div class="tiny card-contact">
    <b>DAN REYES</b><br>Senior Consultant<br>
    (402) 555-0148<br>info@harlowfreight.com<br>www.harlowfreight.com<br>410 Harbor Rd, Ste 12, Norfolk, VA 23510
  </div>
</section>
<section class="piece card-back">
  <div class="brand"><span class="dot" style="width:7px;height:7px"></span>HARLOW</div>
  <div class="web">www.harlowfreight.com</div>
</section>
<div class="label" style="left:68px;top:147px;width:105px">Business card</div>

<!-- Letterhead -->
<section class="piece letterhead">
  <div class="brand" style="position:absolute;left:18px;top:32px;font-size:10px"><span class="dot" style="width:8px;height:8px"></span><span>HARLOW<small>TRANSPORTATION · LOGISTICS</small></span></div>
  <div class="contact-col tiny" style="left:146px;top:28px">
    <div><b>HARLOW</b><br>410 Harbor Rd, Ste 12<br>Norfolk, VA 23510</div>
    <div class="rule"></div>
    <div>(402) 555-0148<br>info@harlowfreight.com<br>www.harlowfreight.com</div>
  </div>
  <div class="faint-mark" style="left:72px;top:150px;width:130px;height:130px"></div>
</section>
<div class="label" style="left:73px;top:567px;width:264px">Letterhead</div>

<!-- Word document letterhead -->
<section class="piece letter">
  <div class="brand" style="position:absolute;left:18px;top:34px;font-size:10px"><span class="dot" style="width:8px;height:8px"></span><span>HARLOW<small>TRANSPORTATION · LOGISTICS</small></span></div>
  <div class="contact-col tiny" style="left:158px;top:28px">
    <div><b>HARLOW</b><br>410 Harbor Rd, Ste 12<br>Norfolk, VA 23510</div>
    <div class="rule"></div>
    <div>(402) 555-0148<br>info@harlowfreight.com<br>www.harlowfreight.com</div>
  </div>
  <div class="tiny" style="position:absolute;left:18px;top:120px;font-size:5px">
    <b>Dan Reyes</b><br>Manager<br>1234 Street Name<br>Brookfield, NC
  </div>
  <div class="tiny" style="position:absolute;right:18px;top:120px;font-size:5px">Date: 31/01/2019</div>
  <div class="body">
    <p>Thank you for choosing our team to move your freight. We have reviewed your shipping schedule and confirmed pickup windows for each route. Our drivers will collect goods at your dock and deliver them safely and on time to every listed destination. Tracking updates will be sent daily, and our dispatch desk is available around the clock for any change in volume or timing. We look forward to a long and steady partnership.</p>
    <p>Please contact our office with questions about rates, insurance or delivery terms at any time.</p>
    <div class="tiny">sincerely</div>
    <div class="signature" role="img" aria-label="Handwritten signature"></div>
    <div class="tiny">Dan Reyes</div>
  </div>
  <div class="faint-mark" style="left:230px;top:300px;width:62px;height:62px;border-width:4px"></div>
</section>
<div class="label" style="left:385px;top:567px;width:285px">Word Document Letterhead</div>

<!-- Envelope front -->
<section class="piece env-front">
  <div class="brand" style="position:absolute;left:22px;top:26px;font-size:13px"><span class="dot" style="width:10px;height:10px"></span><span>HARLOW<small>TRANSPORTATION · LOGISTICS</small></span></div>
  <div class="tiny" style="position:absolute;left:22px;top:54px;font-size:6px;display:flex;align-items:center;gap:3px">
    <svg width="6" height="8" viewBox="0 0 6 8"><path d="M3 0a3 3 0 0 0-3 3c0 2.2 3 5 3 5s3-2.8 3-5a3 3 0 0 0-3-3zm0 4.2a1.2 1.2 0 1 1 0-2.4 1.2 1.2 0 0 1 0 2.4z" fill="#1f5fbf"/></svg>
    410 Harbor Rd, Ste 12, Norfolk, VA 23510
  </div>
  <div class="env-window"></div>
  <div class="faint-mark" style="left:215px;top:10px;width:140px;height:140px"></div>
</section>
<div class="label" style="left:25px;top:778px;width:338px">Envelope Front</div>

<!-- Envelope back -->
<section class="piece env-back">
  <svg class="env-flap" width="334" height="54" viewBox="0 0 334 54"><path d="M0 0h334l-10 54H10z" fill="#0c0c0e"/></svg>
  <div class="brand" style="position:absolute;left:140px;top:22px;font-size:10px;color:var(--blue)"><span class="dot" style="width:7px;height:7px"></span>HARLOW</div>
</section>
<div class="label" style="left:378px;top:778px;width:334px">Envelope Back</div>

<!-- ID card -->
<section class="piece id-card">
  <div class="brand" style="justify-content:center;font-size:9px"><span class="dot" style="width:7px;height:7px"></span><span>HARLOW<small>TRANSPORTATION · LOGISTICS</small></span></div>
  <div class="photo" role="img" aria-label="Employee portrait photo"></div>
  <div class="id-name">DAN REYES</div>
  <div class="id-role">Senior Consultant</div>
  <div class="id-table">
    <span>Id No</span>: 01254<br>
    <span>Email</span>: info@harlowfreight.com<br>
    <span>Phone</span>: (402) 555-0148<br>
    <span>Blood</span>: (A+)
  </div>
</section>
<div class="label" style="left:296px;top:1164px;width:146px">Id card</div>

</body>
</html>
```